Harbourline Electrical Solutions

On one side. LOGO (underneath:) Commercial Industrial Residential

- NAME & CONTACT DETAILS

Marcus T. Hollings
Project Manager

(Cell icon) (441) 555-0187
(Email icon) hlelectricalsolutions@mailvento.com
(Facebook & Instagram icons )@hlelectricalsolutions

Other side: LOGO - underneath ELECTRICAL CONSTRUCTION & MAINTENANCE . LED LIGHTING & AUTOMATION . LIFE SAFETY SYSTEMS (FIRE ALARM / SECURITY) . DATA & COMMUNICATION

```html
<!DOCTYPE html>
<html lang="en">
<head>
<meta charset="utf-8">
<title>Harbourline Electrical Solutions – Business Card</title>
<link rel="stylesheet" href="https://fonts.googleapis.com/css2?family=Poppins:wght@300;400;500;600&display=swap">
<style>
  :root {
    --teal: #0f6f8d;
    --teal-deep: #0a5872;
    --teal-light: #14809f;
    --paper: #f4f5f5;
    --paper-shade: #e6e8e9;
    --ink-grey: #4a4f54;
    --white: #ffffff;
    --backdrop: #d9d6d1;
  }
  * { box-sizing: border-box; margin: 0; padding: 0; }
  html, body { width: 1200px; height: 780px; overflow: hidden; }
  body {
    background: var(--backdrop);
    font-family: "Poppins", sans-serif;
    display: flex;
    align-items: center;
    justify-content: center;
    gap: 60px;
  }
  .card {
    width: 530px;
    height: 303px;
    position: relative;
    overflow: hidden;
    box-shadow: 0 10px 26px rgba(0,0,0,.22);
  }

  /* Front */
  .card-front { background: var(--paper); }
  .front-brand {
    height: 168px;
    background: linear-gradient(180deg, var(--white), var(--paper-shade));
    display: flex;
    flex-direction: column;
    justify-content: center;
    padding-left: 52px;
  }
  .wordmark {
    font-weight: 600;
    text-transform: uppercase;
    letter-spacing: 2px;
    line-height: 1.12;
  }
  .front-brand .wordmark { color: var(--teal); font-size: 25px; }
  .tagline {
    margin-top: 12px;
    font-weight: 400;
    font-size: 12.5px;
    letter-spacing: .4px;
    color: var(--ink-grey);
  }
  .front-contact {
    height: 135px;
    background: linear-gradient(135deg, var(--teal-light), var(--teal-deep));
    display: flex;
    align-items: center;
    padding: 0 30px 0 52px;
    color: var(--white);
  }
  .person { width: 180px; }
  .person-name {
    font-weight: 600;
    font-size: 15px;
    text-transform: uppercase;
    letter-spacing: .3px;
  }
  .person-role { font-weight: 400; font-size: 12.5px; margin-top: 2px; }
  .divider {
    width: 1px;
    height: 78px;
    background: rgba(255,255,255,.75);
    margin: 0 20px;
  }
  .contact-list { list-style: none; font-size: 11.5px; font-weight: 400; }
  .contact-list li { display: flex; align-items: center; gap: 7px; line-height: 1; margin: 8px 0; }
  .icon { width: 13px; height: 13px; flex: none; }
  .icon-pair { display: flex; gap: 3px; }
  .dot { width: 13px; height: 13px; border-radius: 50%; background: var(--white); }

  /* Back */
  .card-back {
    background: radial-gradient(circle at 62% 38%, var(--teal-light), var(--teal-deep) 85%);
    color: var(--white);
    display: flex;
    flex-direction: column;
    align-items: center;
    justify-content: center;
    text-align: center;
  }
  .card-back .wordmark { font-size: 30px; color: var(--white); }
  .services {
    margin-top: 26px;
    font-weight: 300;
    font-size: 11.5px;
    line-height: 1.75;
    letter-spacing: .2px;
  }
</style>
</head>
<body>

  <section class="card card-front" aria-label="Business card front">
    <div class="front-brand">
      <div class="wordmark">Harbourline<br>Electrical Solutions</div>
      <p class="tagline">Commercial Industrial Residential</p>
    </div>
    <div class="front-contact">
      <div class="person">
        <p class="person-name">Marcus T. Hollings</p>
        <p class="person-role">Project Manager</p>
      </div>
      <span class="divider"></span>
      <ul class="contact-list">
        <li>
          <svg class="icon" viewBox="0 0 14 14" aria-hidden="true"><circle cx="7" cy="7" r="7" fill="#fff"/><rect x="4.6" y="3" width="4.8" height="8" rx="1" fill="none" stroke="#0f6f8d" stroke-width="1.1"/><circle cx="7" cy="9.4" r=".6" fill="#0f6f8d"/></svg>
          (441) 555-0187
        </li>
        <li>
          <svg class="icon" viewBox="0 0 14 14" aria-hidden="true"><circle cx="7" cy="7" r="7" fill="#fff"/><rect x="3.5" y="4.5" width="7" height="5" fill="none" stroke="#0f6f8d" stroke-width="1"/><path d="M3.5 4.5 7 7.4 10.5 4.5" fill="none" stroke="#0f6f8d" stroke-width="1"/></svg>
          hlelectricalsolutions@mailvento.com
        </li>
        <li>
          <span class="icon-pair" aria-hidden="true"><span class="dot"></span><span class="dot"></span></span>
          @hlelectricalsolutions
        </li>
      </ul>
    </div>
  </section>

  <section class="card card-back" aria-label="Business card back">
    <div class="wordmark">Harbourline<br>Electrical Solutions</div>
    <p class="services">
      Electrical Construction &amp; Maintenance | LED Lighting &amp; Automation<br>
      Life Safety Systems (FIRE ALARM / SECURITY) | Data &amp; Communication
    </p>
  </section>

</body>
</html>
```